Business Card Design - Photographer

I am a landscape photographer and I require a business card design. 

I require two designs:
1)  a double sided business card
 and
b)  a single sided business card 

The single sided design can either be the same as the double sided (with just one side having all the information)....or it can be an entire new design. Its up to you.

My corporate colours are (CMYK):

Blue   69, 32, 0, 0
Grey  72,  64,  47,  31
Green  32,  2,  91,  0
Yellow   0, 19, 92, 0
Orange  0, 39, 75, 0

Colour space in final file should be in CMYK.

The details that need to be included on the card:

- Use the provided Logo
- Name: Wiktor Baranowski
- Email:   sales@vistalumeworks.com.au
- Website:    vistalumeworks.com.au
- Twitter:    twitter.com/vistalumeworks
- Facebook:   facebook.com/vistalumeworks
- Mobile  0417 539 662

Please use the attached template to design the logo to the specified size, including the marked bleed lines. I have also attached my logo in PNG (transparent background) and ai format for you to use.

The final file should be:
- Photoshop version with layers so I can edit the name/text etc. All non vector files should be high resolution at 1039 x 697 pixels at 300 dpi.

I also require a file as:
- Vector based PDF

Anyway questions please contact me.

Thank you

Industry/Entity Type

Landscape

Logo styles of interest
Pictorial/Combination Logo
Abstract Logo
Wordmark Logo
Lettermark Logo
Requirements
Must have
• The details that need to be included on the card:

- Use the provided Logo
- Name: Wiktor Baranowski
- Email: sales@vistalumeworks.com.au
- Website: vistalumeworks.com.au
- Twitter: twitter.com/vistalumeworks
- Facebook: facebook.com/vistalumeworks
- Mobile 0417 539 662

```html
<!DOCTYPE html>
<html lang="en">
<head>
<meta charset="utf-8">
<title>Vistalume Works – Business Card</title>
<link rel="stylesheet" href="https://fonts.googleapis.com/css2?family=Ubuntu:wght@400;500&display=swap">
<style>
  :root {
    --page: #e6e6e6;
    --ink: #3a3a3a;
    --paper: #f3f2ef;
    --rule: #b9b9b9;
    --blue: #2a86cf;
    --orange: #f7941d;
    --green: #a6c83c;
    --yellow: #fcce10;
    --charcoal: #1c1c1c;
    --logo-grey: #4a4a4a;
    --mark: #5a5a5a;
  }
  html, body {
    margin: 0;
    width: 1200px;
    height: 800px;
    overflow: hidden;
    background: var(--page);
    font-family: "Ubuntu", sans-serif;
  }
  .stage { position: relative; width: 1200px; height: 800px; }
  .card {
    position: absolute;
    top: 240px;
    width: 560px;
    height: 320px;
    overflow: hidden;
  }

  /* Back side */
  .card--back {
    left: 20px;
    background: radial-gradient(ellipse at 50% 40%, #2b2e31 0%, #141516 45%, #000 80%);
  }
  .crop-marks { position: absolute; inset: 0; }
  .back-logo {
    position: absolute;
    left: 0; right: 0; top: 96px;
    display: flex; flex-direction: column; align-items: center;
  }
  .back-logo__dot {
    width: 64px; height: 64px; border-radius: 50%;
    background: var(--logo-grey);
  }
  .back-logo__name {
    margin-top: 22px;
    font-size: 24px; font-weight: 400; letter-spacing: 1.5px;
    color: var(--logo-grey);
    text-transform: uppercase;
  }

  /* Front side */
  .card--front {
    left: 620px;
    background: var(--paper);
    box-shadow: inset 0 0 0 1px #fff;
  }
  .tree-art {
    position: absolute;
    left: 4px; top: 6px;
    width: 118px; height: 236px;
    background: linear-gradient(160deg, var(--green) 0%, var(--orange) 25%, var(--blue) 48%, var(--yellow) 65%, #222 80%, var(--green) 100%);
    border-radius: 40px 60px 60px 20px;
    opacity: .9;
  }
  .front-logo {
    position: absolute;
    right: 26px; top: 24px;
    width: 180px;
    display: flex; flex-direction: column; align-items: center;
  }
  .front-logo__dot {
    width: 56px; height: 56px; border-radius: 50%;
    background: var(--charcoal);
  }
  .front-logo__name {
    margin-top: 14px;
    font-size: 16px; font-weight: 400; letter-spacing: 1px;
    color: var(--charcoal);
    text-transform: uppercase;
  }
  .holder-name {
    position: absolute;
    left: 205px; top: 157px;
    font-size: 17px; font-weight: 500;
    color: var(--blue);
  }
  .website {
    position: absolute;
    left: 29px; top: 225px;
    font-size: 16px;
    color: var(--orange);
  }
  .divider {
    position: absolute;
    left: 0; right: 0; top: 250px;
    height: 1px; background: var(--rule);
  }
  .contacts {
    position: absolute;
    top: 259px;
    margin: 0; padding: 0; list-style: none;
    font-size: 12.5px; color: var(--ink);
  }
  .contacts li { display: flex; align-items: center; height: 18px; }
  .contacts svg, .contacts .social-dot { margin-right: 6px; flex: none; }
  .contacts--direct { left: 28px; }
  .contacts--social { left: 311px; }
  .social-dot {
    width: 12px; height: 12px; border-radius: 2px;
    background: var(--blue);
  }
</style>
</head>
<body>
<main class="stage">

  <section class="card card--back" aria-label="Card back">
    <svg class="crop-marks" width="560" height="320" viewBox="0 0 560 320" aria-hidden="true">
      <g fill="none" stroke="var(--mark)" stroke-width="2">
        <path d="M66 89 V77 H78"/>
        <path d="M482 77 H494 V89"/>
        <path d="M66 233 V245 H78"/>
        <path d="M482 245 H494 V233"/>
      </g>
    </svg>
    <div class="back-logo">
      <span class="back-logo__dot"></span>
      <span class="back-logo__name">Vistalume Works</span>
    </div>
  </section>

  <section class="card card--front" aria-label="Card front">
    <div class="tree-art" role="img" aria-label="Illustrated tree with colourful blue, orange, green, yellow and black leaves"></div>

    <div class="front-logo">
      <span class="front-logo__dot"></span>
      <span class="front-logo__name">Vistalume Works</span>
    </div>

    <p class="holder-name" style="margin:0">Wiktor Baranowski</p>
    <p class="website" style="margin:0">www.vistalumeworks.com.au</p>
    <div class="divider"></div>

    <ul class="contacts contacts--direct">
      <li>
        <svg width="12" height="14" viewBox="0 0 12 14" aria-hidden="true">
          <rect x="3" y="1" width="7" height="12" rx="1.5" fill="none" stroke="var(--blue)" stroke-width="1.4"/>
          <circle cx="6.5" cy="11" r=".8" fill="var(--blue)"/>
        </svg>
        0417 539 662
      </li>
      <li>
        <svg width="12" height="10" viewBox="0 0 12 10" aria-hidden="true">
          <rect x=".5" y="1" width="11" height="8" fill="var(--blue)"/>
          <path d="M.5 1 L6 5.5 L11.5 1" fill="none" stroke="#fff" stroke-width="1"/>
        </svg>
        sales@vistalumeworks.com.au
      </li>
    </ul>

    <ul class="contacts contacts--social">
      <li><span class="social-dot"></span>vistalumeworks</li>
      <li><span class="social-dot"></span>vistalumeworks</li>
    </ul>
  </section>

</main>
</body>
</html>
```